Counseling Practice Business Card

I need a professional looking business card incorporating my new logo that was just completed. Card needs to incorporate my name and title, description of my specialty, my address, my phone number, my fax number, my email and my website URL. I need to be able to choose design on/with different paper colors and textures.
I do not have a lot of business card ideas so I am open to anything but I want bold,sharp, clear card without additional designs other than my logo (see attached file info). I am open to different color backgrounds or paper colors including black. I do not like traditional brackets around area codes in phone number or dashes between numbers in phone number. Am open to other ways of presenting including periods between numbers as appropriate. I do not know enough to know what I like yet but I want card to coordinate and work together with my logo. My practice emphasizes natural mental health interventions so any use of color (with background paper color or the blue and green in my logo) that elicits nature is nice. In addition to black, any natural brown or wood looking background might be desirable also. Most of the offerings so far look very similar and boring.

Target Market(s)

Potential therapy clients and other professionals

Contact Information for Business Card

Card information:
Gerald M. Whitcombe, Ph.D.
Licensed Clinical Psychologist
Integrative Health Coach
4812 Marlowe Ridge Blvd SE
Suite 310
Cedarbrook, GA 30217
(770) 415-2983 phone
(770) 581-4096 fax
drgeraldwhitcombe@quillmarsh.net
brightfernwellness.net

Font styles to use
Serif
Sans Serif
Other font styles liked:
• anything that you think looks crisp, clear and easily readable

Requirements
Must have
• Any color used should coordinate with my logo design (see attached files).
• Card should be printed horizontally so top and bottom are longest sides of rectangle.
• Background color or paper color should complement and highlight logo. Do not like a white background. black, grey, brown or any color my logo would blend well with.
Nice to have
• I would like designer to utilize color to highlight letters/name or phone-fax-web symbols.
• Bottom edge of card could be highlighted if appropriate to an idea.
Should not have
• I would NOT want the card to have a pure white background at all.
• No clear cards.
• Cards should be oriented with long sides on bottom and top, NOT sides. DO NOT LIKE THIS THIN TALL ORIENTATION.

```html
<!DOCTYPE html>
<html lang="en">
<head>
<meta charset="utf-8">
<title>Brightfern Wellness – Business Card</title>
<link href="https://fonts.googleapis.com/css2?family=PT+Sans:wght@400;700&display=swap" rel="stylesheet">
<style>
  :root {
    --canvas: #e9e6e1;
    --card-black: #131416;
    --card-charcoal: #2a2c30;
    --brand-blue: #2f7fc4;
    --brand-green: #1c7a45;
    --text-white: #ffffff;
    --text-soft: #e6eef7;
    --text-grey: #9a9ea4;
  }
  * { box-sizing: border-box; margin: 0; padding: 0; }
  html, body { width: 1200px; height: 950px; overflow: hidden; }
  body {
    background: var(--canvas);
    font-family: "PT Sans", Arial, sans-serif;
    display: flex;
    flex-direction: column;
    align-items: center;
    justify-content: center;
    gap: 50px;
  }
  .card {
    position: relative;
    width: 700px;
    height: 400px;
    overflow: hidden;
    border-radius: 4px;
    box-shadow: 0 6px 18px rgba(0,0,0,0.25);
  }
  .card-front {
    background: linear-gradient(200deg, var(--card-charcoal) 0%, var(--card-black) 60%);
  }
  .card-back { background: var(--card-black); }
  .front-shapes { position: absolute; inset: 0; }

  .brand-name {
    font-family: "PT Sans", Arial, sans-serif;
    font-weight: 700;
    color: var(--brand-blue);
    white-space: nowrap;
  }
  .front-brand {
    position: absolute;
    left: 30px;
    top: 182px;
    font-size: 26px;
  }

  .contact-block {
    position: absolute;
    right: 24px;
    top: 34px;
    bottom: 30px;
    width: 390px;
    text-align: right;
    color: var(--text-white);
    display: flex;
    flex-direction: column;
    justify-content: space-between;
  }
  .holder-name {
    font-weight: 700;
    font-size: 21px;
    text-transform: uppercase;
    letter-spacing: 0.3px;
    white-space: nowrap;
  }
  .holder-title { font-size: 15px; color: var(--text-soft); line-height: 1.35; white-space: nowrap; }
  .contact-lines { font-size: 12px; line-height: 1.6; color: var(--text-soft); white-space: nowrap; }

  .back-brand {
    position: absolute;
    left: 50%;
    top: 50%;
    transform: translate(-50%, -50%);
    font-size: 44px;
  }
  .back-url {
    position: absolute;
    left: 44px;
    top: 50%;
    transform: translate(-50%, -50%) rotate(90deg);
    font-size: 13px;
    letter-spacing: 5px;
    color: var(--text-grey);
    white-space: nowrap;
  }
</style>
</head>
<body>

  <section class="card card-front" aria-label="Business card front">
    <svg class="front-shapes" viewBox="0 0 700 400" preserveAspectRatio="none" aria-hidden="true">
      <path class="green-band" d="M420 0 C326 70 270 210 270 400 L300 400 C300 210 356 70 450 0 Z" fill="#1c7a45"/>
      <path class="blue-panel" d="M450 0 C356 70 300 210 300 400 L700 400 L700 0 Z" fill="#2f7fc4"/>
    </svg>

    <div class="brand-name front-brand">Brightfern Wellness</div>

    <div class="contact-block">
      <div>
        <p class="holder-name">Gerald M. Whitcombe, Ph.D.</p>
        <p class="holder-title">Licensed Clinical Psychologist</p>
        <p class="holder-title">Integrative Health Coach</p>
      </div>
      <div class="contact-lines">
        <p>M. (770) 415-2983 F. (770) 581-4096</p>
        <p>drgeraldwhitcombe@quillmarsh.net | www.brightfernwellness.net</p>
        <p>4812 Marlowe Ridge Blvd SE, Suite 310, Cedarbrook, GA 30217</p>
      </div>
    </div>
  </section>

  <section class="card card-back" aria-label="Business card back">
    <div class="back-url">www.brightfernwellness.net</div>
    <div class="brand-name back-brand">Brightfern Wellness</div>
  </section>

</body>
</html>
```